Veldmark Supplies Business Card

Professional business card that stand out to our potential customers. Front and back with clean modern design

Industry/Entity Type

Oil and gas

Contact Information for Business Card

Name, address, website , office phone and cell number

Requirements
Must have
• Editable files for each employee

```html
<!DOCTYPE html>
<html lang="en">
<head>
<meta charset="utf-8">
<title>Veldmark Supplies – Business Card</title>
<link rel="stylesheet" href="https://fonts.googleapis.com/css2?family=Montserrat:wght@400;500;800&display=swap">
<style>
  :root {
    --page: #e4e4e4;
    --card: #2b2b2d;
    --red: #e8212b;
    --cyan: #1aafd0;
    --white: #f4f4f4;
    --pattern-cool: #4d7e92;
    --pattern-mid: #7a6660;
    --pattern-warm: #c8412e;
  }
  * { box-sizing: border-box; margin: 0; padding: 0; }
  html, body { width: 1200px; height: 856px; overflow: hidden; }
  body {
    background: var(--page);
    font-family: "Montserrat", sans-serif;
    display: flex;
    align-items: center;
    justify-content: center;
    gap: 40px;
  }
  .card {
    width: 540px;
    height: 309px;
    background: var(--card);
    position: relative;
    overflow: hidden;
    box-shadow: 0 10px 28px rgba(0,0,0,0.25);
  }

  /* Front */
  .brand {
    position: absolute;
    left: 36px;
    top: 0;
    bottom: 0;
    width: 210px;
    display: flex;
    align-items: center;
    gap: 10px;
  }
  .brand-mark {
    width: 14px;
    height: 14px;
    background: var(--red);
    flex: none;
  }
  .brand-name {
    color: var(--red);
    font-weight: 800;
    font-size: 19px;
    letter-spacing: 0.5px;
    text-transform: uppercase;
    line-height: 1.2;
  }
  .divider {
    position: absolute;
    left: 262px;
    top: 58px;
    bottom: 58px;
    width: 2px;
    background: var(--red);
  }
  .details {
    position: absolute;
    left: 286px;
    top: 52px;
    color: var(--white);
  }
  .person-name {
    color: var(--red);
    font-weight: 800;
    font-size: 21px;
    letter-spacing: 0.3px;
    text-transform: uppercase;
  }
  .person-title {
    font-size: 12px;
    font-weight: 500;
    margin-top: 2px;
  }
  .address {
    font-size: 11px;
    line-height: 1.45;
    margin-top: 14px;
  }
  .contact-list {
    list-style: none;
    margin-top: 12px;
  }
  .contact-list li {
    display: flex;
    align-items: center;
    gap: 9px;
    font-size: 11px;
    line-height: 1;
    margin-bottom: 7px;
  }
  .contact-icon {
    width: 16px;
    height: 16px;
    background: var(--red);
    flex: none;
    display: flex;
    align-items: center;
    justify-content: center;
  }
  .contact-icon svg { width: 11px; height: 11px; }

  /* Back */
  .pattern-field {
    position: absolute;
    inset: 0;
    background: linear-gradient(200deg, var(--pattern-warm) 0%, var(--pattern-warm) 30%, var(--pattern-mid) 62%, var(--pattern-cool) 100%);
    opacity: 0.55;
  }
  .back-brand {
    position: absolute;
    right: 64px;
    top: 200px;
    display: flex;
    align-items: center;
    gap: 7px;
  }
  .back-brand .brand-mark { width: 10px; height: 10px; }
  .back-brand .brand-name {
    color: var(--white);
    font-size: 12px;
  }
</style>
</head>
<body>

  <section class="card card-front">
    <div class="brand">
      <span class="brand-mark"></span>
      <span class="brand-name">Veldmark Supplies</span>
    </div>

    <div class="divider"></div>

    <div class="details">
      <h1 class="person-name">Dorin Halvec</h1>
      <p class="person-title">President</p>
      <p class="address">482 Larkspur Row, Ste<br>210, Corvale, TX 70418</p>
      <ul class="contact-list">
        <li>
          <span class="contact-icon">
            <svg viewBox="0 0 12 12"><path fill="#fff" d="M2.4 1h2l1 2.6-1.3 1a6 6 0 0 0 3.3 3.3l1-1.3L11 7.6v2A1.4 1.4 0 0 1 9.6 11 8.6 8.6 0 0 1 1 2.4 1.4 1.4 0 0 1 2.4 1z"/></svg>
          </span>
          555-014-2273
        </li>
        <li>
          <span class="contact-icon">
            <svg viewBox="0 0 12 12"><rect x="3" y="0.8" width="6" height="10.4" rx="1" fill="none" stroke="#fff" stroke-width="1.3"/><circle cx="6" cy="9.3" r="0.7" fill="#fff"/></svg>
          </span>
          555-018-6640
        </li>
        <li>
          <span class="contact-icon">
            <svg viewBox="0 0 12 12"><rect x="0.8" y="2.2" width="10.4" height="7.6" fill="none" stroke="#fff" stroke-width="1.2"/><path d="M1 2.5 6 6.6 11 2.5" fill="none" stroke="#fff" stroke-width="1.2"/></svg>
          </span>
          hello@veldmark-mail.com
        </li>
        <li>
          <span class="contact-icon">
            <svg viewBox="0 0 12 12"><circle cx="6" cy="6" r="5" fill="none" stroke="#fff" stroke-width="1.1"/><ellipse cx="6" cy="6" rx="2.2" ry="5" fill="none" stroke="#fff" stroke-width="1"/><path d="M1 6h10" stroke="#fff" stroke-width="1"/></svg>
          </span>
          www.veldmark-supply.com
        </li>
      </ul>
    </div>
  </section>

  <section class="card card-back">
    <div class="pattern-field" role="img" aria-label="Repeating brand-mark pattern fading from steel blue to red across the card"></div>
    <div class="back-brand">
      <span class="brand-mark"></span>
      <span class="brand-name">Veldmark Supplies</span>
    </div>
  </section>

</body>
</html>
```